VELMOR Website Design

We need a website designed for our company VELMOR. We are a luxury lifestyle club that will provide benefits and services for our members. The site should be clean & sleek, preferably using black and white (or darker colors). (example sites: stravenhall.example, plinth.example)

Here is a link of a sample page I did using wix. (https://dunmere7.sitehostly.example/mysite) This can be used to get a general idea.

Target Market(s)

Upper Middle Class in the United States

Number of Pages Required

5+ page

Font styles to use
Sans Serif
Other font styles liked:
• Arial (or other similar fonts)

Requirements
Must have
• A clean design that is eye-catching and speaks to our company.
Nice to have
• Ideas for copy.

```html
<!DOCTYPE html>
<html lang="en">
<head>
<meta charset="UTF-8">
<title>VELMOR — A Members Only Lifestyle Club</title>
<link rel="stylesheet" href="https://fonts.googleapis.com/css2?family=Montserrat:wght@300;400;500;600&display=swap">
<style>
  :root {
    --night: #070b18;
    --night-deep: #05080f;
    --pentagon-top: #06142a;
    --pentagon-bottom: #0e1b44;
    --ink: #ffffff;
    --ink-soft: #d9dde6;
    --ink-muted: #c3c8d4;
    --rule: #8a93a8;
    --hero-a: #2a2f38;
    --hero-b: #5a4a3e;
    --hero-c: #1a1c22;
    --photo-a: #d8d8d8;
    --photo-b: #5a5a5a;
    --photo-c: #1e1e1e;
  }
  * { margin: 0; padding: 0; box-sizing: border-box; }
  html, body { width: 1032px; height: 1200px; overflow: hidden; }
  body {
    position: relative;
    background: var(--night);
    font-family: "Montserrat", Arial, sans-serif;
    color: var(--ink);
  }
  .site-header {
    position: absolute; left: 0; top: 0; width: 1032px; height: 84px;
    background: var(--night); z-index: 3;
  }
  .brand {
    position: absolute; left: 130px; top: 26px;
    font-size: 26px; font-weight: 400; letter-spacing: 1.5px;
  }
  .main-nav { position: absolute; top: 35px; left: 0; width: 100%; }
  .main-nav a {
    position: absolute; font-size: 11px; font-weight: 400;
    color: var(--ink-soft); text-decoration: none; letter-spacing: 0.4px;
    white-space: nowrap;
  }
  .main-nav a.is-current { color: var(--ink); font-weight: 600; }
  .hero {
    position: absolute; left: 0; top: 84px; width: 1032px; height: 687px;
    background:
      radial-gradient(ellipse at 78% 20%, rgba(120,90,80,0.55), transparent 45%),
      radial-gradient(ellipse at 12% 55%, rgba(150,120,100,0.5), transparent 40%),
      radial-gradient(ellipse at 40% 35%, rgba(160,170,180,0.35), transparent 45%),
      linear-gradient(180deg, var(--hero-a) 0%, var(--hero-b) 55%, var(--hero-c) 100%);
  }
  .hero-title {
    position: absolute; left: 263px; top: 181px; width: 506px; height: 70px;
    border: 1.5px solid rgba(255,255,255,0.75);
    display: flex; align-items: center; justify-content: center;
    font-size: 28px; font-weight: 500; letter-spacing: 0.6px; z-index: 2;
  }
  .footer-rule {
    position: absolute; top: 1097px; height: 1px; background: var(--rule);
  }
  .footer-rule.left { left: 3px; width: 206px; }
  .footer-rule.right { left: 828px; width: 199px; }
  .pentagon {
    position: absolute; left: 0; top: 0; width: 1032px; height: 1200px;
    z-index: 1;
  }
  .about {
    position: absolute; left: 0; top: 0; width: 1032px; z-index: 2;
  }
  .about-heading {
    position: absolute; left: 0; top: 384px; width: 1032px; text-align: center;
    font-weight: 300; line-height: 42px;
  }
  .about-heading .eyebrow { display: block; font-size: 40px; }
  .about-heading .name { display: block; font-size: 41px; font-weight: 400; letter-spacing: 2px; }
  .about-rule {
    position: absolute; left: 401px; top: 475px; width: 229px; height: 1px;
    background: var(--rule);
  }
  .about-photo {
    position: absolute; left: 323px; top: 515px; width: 386px; height: 264px;
    background:
      radial-gradient(ellipse at 55% 30%, var(--photo-a), transparent 35%),
      linear-gradient(180deg, var(--photo-b) 0%, var(--photo-c) 55%, var(--photo-b) 100%);
  }
  .about-copy {
    position: absolute; left: 271px; top: 814px; width: 500px;
    font-size: 15px; line-height: 26px; color: var(--ink-soft); letter-spacing: 0.2px;
  }
  .about-copy p + p { margin-top: 26px; }
  .learn-more {
    position: absolute; left: 455px; top: 992px; width: 122px; height: 37px;
    border: 1.5px solid var(--ink); border-radius: 19px;
    display: flex; align-items: center; justify-content: center;
    font-size: 12px; font-weight: 500; color: var(--ink); text-decoration: none;
  }
  .slider-dots { position: absolute; top: 1058px; left: 485px; display: flex; gap: 16px; }
  .slider-dots span {
    width: 10px; height: 10px; border-radius: 50%; border: 1px solid var(--ink-soft);
  }
  .slider-dots span.is-active { background: var(--ink-soft); }
  .contact-rule {
    position: absolute; left: 259px; top: 1097px; width: 514px; height: 1px;
    background: var(--rule);
  }
  .contact-label {
    position: absolute; left: 0; top: 1112px; width: 1032px; text-align: center;
    font-size: 10.5px; font-weight: 600; letter-spacing: 0.3px;
  }
  .social-links {
    position: absolute; top: 1132px; left: 467px; display: flex; gap: 9px;
  }
  .social-links span {
    width: 13px; height: 13px; border-radius: 50%; background: var(--ink-muted);
  }
</style>
</head>
<body>
  <header class="site-header">
    <div class="brand">VELMOR</div>
    <nav class="main-nav">
      <a class="is-current" href="#" style="left:528px">HOME</a>
      <a href="#" style="left:587px">ABOUT</a>
      <a href="#" style="left:649px">SERVICES AND BENEFITS</a>
      <a href="#" style="left:815px">APPLY</a>
      <a href="#" style="left:874px">CONTACT</a>
    </nav>
  </header>

  <section class="hero" role="img" aria-label="Photo of friends raising wine glasses in a toast"></section>
  <h1 class="hero-title">A Members Only Lifestyle Club</h1>

  <div class="footer-rule left"></div>
  <div class="footer-rule right"></div>

  <svg class="pentagon" viewBox="0 0 1032 1200" aria-hidden="true">
    <defs>
      <linearGradient id="pentagonFill" x1="0" y1="0" x2="0" y2="1">
        <stop offset="0" stop-color="var(--pentagon-top)"/>
        <stop offset="1" stop-color="var(--pentagon-bottom)"/>
      </linearGradient>
      <filter id="pentagonShadow" x="-10%" y="-10%" width="120%" height="120%">
        <feDropShadow dx="0" dy="6" stdDeviation="10" flood-color="#000" flood-opacity="0.55"/>
      </filter>
    </defs>
    <polygon points="515,285 979,620 806,1166 231,1168 53,624"
             fill="url(#pentagonFill)" fill-opacity="0.96" filter="url(#pentagonShadow)"/>
  </svg>

  <main class="about">
    <h2 class="about-heading">
      <span class="eyebrow">About</span>
      <span class="name">VELMOR</span>
    </h2>
    <div class="about-rule"></div>
    <div class="about-photo" role="img" aria-label="Black and white photo of members bumping fists over a table"></div>
    <div class="about-copy">
      <p>VELMOR is a members only lifestyle club founded in order to bring the best services, experiences, and opportunities to our diverse community of members.</p>
      <p>Our members consist of creatives, atheletes, artists, and other professionals.</p>
    </div>
    <a class="learn-more" href="#">Learn More</a>
    <div class="slider-dots"><span class="is-active"></span><span></span><span></span></div>
    <div class="contact-rule"></div>
    <div class="contact-label">CONTACT US</div>
    <div class="social-links" aria-label="Social links">
      <span></span><span></span><span></span><span></span><span></span>
    </div>
  </main>
</body>
</html>
```